Gospel Tract titled "A Lantern Trail Toward Bright Skies."

This will be a bi-fold brochure. The design will be in the front panel of the brochure which is 4 inches wide and 8.5 inches high. This is a common brochure among Gospel tracts in the series, "A lantern trail toward bright skies ______________ ." The blank is usually a state, city, or other location. I want a "fun" image of Iowa or something representing Iowa at the bottom. A graphic representing "heaven" at the top. Perhaps a meandering road between the two. The words, "A Lantern Trail Toward Bright Skies", but be on the front somewhere. I am also open to other designs with this theme and the words "A Lantern Trail Toward Bright Skies." My suggestion is just one idea.

Target Market(s)

Non-Christians who are interested in knowing how to get to heaven

Requirements
Must have
• Something specific to the state of Iowa at the bottom: farms, state fair, cows, barns, power windmills, the capitol building, etc.
Nice to have
• I would like something bright, colorful, with a fun Iowa image at the bottom.
Should not have
• Religous symbolism....no doves, angels, crosses, etc.

```html
<!DOCTYPE html>
<html lang="en">
<head>
<meta charset="utf-8">
<title>A Lantern Trail Toward Bright Skies From Iowa – Tract Spreads</title>
<link rel="stylesheet" href="https://fonts.googleapis.com/css2?family=Montserrat:wght@400;500;600;700;800;900&family=Great+Vibes&display=swap">
<style>
:root{
  --bg:#b9bfcf;
  --teal-deep:#163c48;
  --gold:#d9b75a;
  --gold-soft:#e7c873;
  --orange:#c8773f;
  --blue-title:#2f5d86;
  --white:#ffffff;
  --ink:#1d2a33;
  --lab-yellow:#f4e27a;
  --lab-cyan:#63d6dc;
  --lab-lime:#b9f04d;
  --lab-blue:#86cdf2;
  --ref-gold:#e6b653;
  --ref-cyan:#4fd0ff;
  --ref-lime:#a6ff3a;
}
*{margin:0;padding:0;box-sizing:border-box}
html,body{width:1200px;height:2400px;overflow:hidden;background:var(--bg)}
body{font-family:"Montserrat",sans-serif;color:var(--white);position:relative}
.spread{position:absolute;left:70px;width:1060px;height:1126px;display:flex;box-shadow:0 6px 18px rgba(0,0,0,.25)}
.spread--outside{top:50px}
.spread--inside{top:1224px}
.panel{position:relative;width:530px;height:1126px;overflow:hidden}
.abs{position:absolute;left:0;right:0;text-align:center}
.panel--dark{background:linear-gradient(180deg,#1d4c58 0%,#163f4b 45%,#143844 75%,#1a4550 100%)}

/* back panel */
.journey-title{top:52px;font-weight:900;line-height:.95;letter-spacing:.5px}
.journey-title .gold{display:block;color:var(--gold);font-size:44px}
.journey-title .white{display:block;color:var(--white);font-size:28px;letter-spacing:2px;margin-top:4px}
.script{font-family:"Great Vibes",cursive;font-weight:400}
.congrats{top:178px;font-size:50px;color:#7fb8bd}
.intro{top:244px;font-size:15px;line-height:1.2;padding:0 100px}
.pill{position:absolute;left:64px;width:409px;height:77px;border-radius:28px;text-align:center;padding-top:13px;font-size:13.5px;line-height:1.25}
.pill h3{font-size:13px;font-weight:800;letter-spacing:2px;margin-bottom:3px}
.pill--olive{top:320px;background:rgba(141,138,92,.85)}
.pill--olive h3{color:var(--lab-yellow)}
.pill--teal{top:406px;background:rgba(47,127,130,.85)}
.pill--teal h3{color:var(--lab-cyan)}
.pill--green{top:492px;background:rgba(123,154,54,.85)}
.pill--green h3{color:var(--lab-lime)}
.pill--steel{top:579px;background:rgba(77,127,153,.8)}
.pill--steel h3{color:var(--lab-blue)}
.reach{top:694px;font-size:14.5px;line-height:1.25;padding:0 120px}
.icon-row{position:absolute;top:752px;left:155px;width:220px;height:26px}
.contact{top:796px;font-size:14.5px;line-height:1.23}
.contact .gap{margin-top:14px}
.verse-foot{top:1020px;font-size:14.5px;line-height:1.2;padding:0 130px}
.qmark{position:absolute;font-family:Georgia,serif;font-weight:700;line-height:1}

/* cover */
.cover-photo{position:absolute;inset:0;background:
  radial-gradient(ellipse 30% 38% at 50% 45%,rgba(255,250,225,.95) 0%,rgba(255,240,200,.55) 40%,rgba(255,255,255,0) 75%),
  linear-gradient(180deg,#3b5d86 0%,#6a7fa0 12%,#c8a486 24%,#8d8ba6 42%,#5f6784 58%,#6f7385 72%)}
.cover-iowa{position:absolute;left:0;right:0;top:800px;bottom:0;background:
  linear-gradient(180deg,rgba(111,115,133,0) 0%,#6f7a5a 14%,#5b6a34 34%,#4c5626 60%,#3d3a22 100%)}
.cover-title{top:58px}
.cover-title .script{display:block;font-size:46px;color:#1e2d44;line-height:1.05}
.cover-title .big{display:block;font-weight:900;line-height:.98;letter-spacing:1px}
.big--skies{color:var(--orange);font-size:50px}
.big--from{color:var(--orange);font-size:66px}
.big--state{color:var(--blue-title);font-size:84px}
.road-line{top:946px;font-size:20px;letter-spacing:1px}
.road-strong{top:976px;font-size:40px;font-weight:900}
.cover-web{top:1055px;font-size:19px;letter-spacing:2px;color:var(--gold-soft)}

/* inside left */
.sky-photo{position:absolute;inset:0;background:
  linear-gradient(180deg,#7f9fc4 0%,#a9c0dc 14%,#e6c7a8 30%,#f1b38e 40%,#c9c9d8 55%,#b8cde0 68%,#9db7cc 80%,#6d7c4a 90%,#4a5a2d 100%)}
.why-title{position:absolute;left:50px;top:44px;font-weight:900;font-size:40px;line-height:.95;color:var(--teal-deep)}
.qpill{position:absolute;left:50px;width:409px;height:76px;border-radius:30px;display:flex;align-items:center;padding-left:66px;padding-right:20px;font-size:14.5px;font-weight:700;line-height:1.25}
.qpill--gold{top:154px;background:rgba(196,160,86,.85)}
.qpill--teal{top:247px;background:rgba(58,140,130,.85)}
.qpill .q{position:absolute;left:20px;top:14px;font-size:44px;font-weight:900}
.good-news{position:absolute;left:55px;top:348px;width:420px;font-size:17px;line-height:1.2;color:var(--ink);font-weight:500}
.glass{position:absolute;left:55px;width:424px;border-radius:26px;background:rgba(255,255,255,.3);color:var(--ink);padding:44px 40px 0 44px;font-size:16.5px;line-height:1.22}
.glass .ref{display:block;margin-top:12px;font-weight:700;font-size:16px}
.glass--one{top:480px;height:184px}
.glass--two{top:710px;height:194px}

/* inside right */
.way-title{top:40px}
.way-title .script{display:block;font-size:58px;line-height:.9;color:var(--white)}
.way-title .caps{display:block;font-weight:900;font-size:38px;color:var(--gold);margin-top:-4px}
.step{position:absolute;left:85px;width:382px;border-radius:24px;text-align:center;padding:34px 28px 0;font-size:13.5px;line-height:1.22}
.step .ref{display:block;font-weight:700;font-size:14px;margin-top:10px}
.step--1{top:186px;height:157px;background:rgba(100,145,120,.75)}
.step--1 .ref{color:var(--ref-gold)}
.step--2{top:369px;height:157px;background:rgba(47,110,135,.75)}
.step--2 .ref{color:var(--ref-cyan)}
.step--3{top:549px;height:161px;background:rgba(77,143,46,.85)}
.step--3 .ref{color:var(--ref-lime)}
.step--4{top:732px;height:163px;background:rgba(47,106,134,.75)}
.step--4 .ref{color:var(--ref-cyan)}
.prayer{top:934px;font-size:15.5px;line-height:1.24;padding:0 90px}
</style>
</head>
<body>

<section class="spread spread--outside">
  <div class="panel panel--dark back-panel">
    <h2 class="abs journey-title"><span class="gold">YOUR<br>JOURNEY</span><span class="white">CONTINUES</span></h2>
    <p class="abs script congrats">Congratulations!</p>
    <p class="abs intro">If you have accepted Jesus as your Savior, you are now on the path to heaven. What's next?</p>

    <div class="pill pill--olive"><h3>READ THE BIBLE</h3>Start with the book of John to learn<br>more about Jesus.</div>
    <div class="pill pill--teal"><h3>PRAY DAILY</h3>Talk to God as you would a friend</div>
    <div class="pill pill--green"><h3>FIND A CHURCH</h3>Join a community of believers who can<br>support and guide you.</div>
    <div class="pill pill--steel"><h3>SHARE THE GOOD NEWS</h3>Talk to God as you would a friend</div>

    <p class="abs reach">If you have questions or want more resources, reach out to us at</p>

    <svg class="icon-row" viewBox="0 0 220 26" aria-hidden="true">
      <g stroke="#7fa7a0" stroke-width="1.2">
        <line x1="0" y1="11" x2="44" y2="11"/><line x1="0" y1="15" x2="44" y2="15"/>
        <line x1="176" y1="11" x2="220" y2="11"/><line x1="176" y1="15" x2="220" y2="15"/>
      </g>
      <g fill="#c9d36a">
        <circle cx="62" cy="13" r="11"/><circle cx="92" cy="13" r="11"/>
        <circle cx="122" cy="13" r="11"/><circle cx="152" cy="13" r="11"/>
      </g>
      <g fill="#1b4450" stroke="#1b4450">
        <path d="M62 6a4.5 4.5 0 0 1 4.5 4.5c0 3.5-4.5 8-4.5 8s-4.5-4.5-4.5-8A4.5 4.5 0 0 1 62 6z" stroke="none"/>
        <circle cx="62" cy="10.5" r="1.6" fill="#c9d36a" stroke="none"/>
        <path d="M87.5 7.5c1-1 2-.8 2.5.3l1 2c.3.7 0 1.2-.6 1.6.8 1.6 1.9 2.7 3.5 3.5.4-.6.9-.9 1.6-.6l2 1c1.1.5 1.3 1.5.3 2.5-2.5 2.5-12-7-10.3-10.3z" stroke="none"/>
        <rect x="116" y="8.5" width="12" height="9" rx="1" fill="none" stroke-width="1.6"/>
        <path d="M116 9l6 5 6-5" fill="none" stroke-width="1.6"/>
        <circle cx="152" cy="13" r="6" fill="none" stroke-width="1.5"/>
        <path d="M146 13h12M152 7c-3 3.5-3 8.5 0 12M152 7c3 3.5 3 8.5 0 12" fill="none" stroke-width="1.2"/>
      </g>
    </svg>

    <div class="abs contact">
      <p>3403 Orchard Row</p>
      <p>Maple Hollow, IA 50210</p>
      <p>City: Maple Hollow</p>
      <p>State: Iowa</p>
      <p>Zip: 50210</p>
      <p class="gap">555 0142 7788</p>
      <p class="gap">hello@lanterntrail.org</p>
      <p class="gap">www.lanterntrail.org</p>
    </div>

    <span class="qmark" style="left:84px;top:1008px;font-size:60px;color:#4c7f86">“</span>
    <p class="abs verse-foot">I have come that they may have life, and have it to the full</p>
    <span class="qmark" style="left:418px;top:1032px;font-size:60px;color:#4c7f86">”</span>
  </div>

  <div class="panel cover-panel">
    <div class="cover-photo" role="img" aria-label="Photo of a stone stairway rising into glowing clouds and a bright sky"></div>
    <div class="cover-iowa" role="img" aria-label="Iowa countryside at the bottom: a dirt road winding through cornfields past a red barn and wind turbines"></div>
    <h1 class="abs cover-title">
      <span class="script">A Lantern Trail Toward</span>
      <span class="big big--skies">BRIGHT SKIES</span>
      <span class="big big--from">FROM</span>
      <span class="big big--state">IOWA</span>
    </h1>
    <p class="abs road-line">THE ROAD STARTS RIGHT</p>
    <p class="abs road-strong">WHERE YOU ARE</p>
    <p class="abs cover-web">www.lanterntrail.org</p>
  </div>
</section>

<section class="spread spread--inside">
  <div class="panel why-panel">
    <div class="sky-photo" role="img" aria-label="Photo of a pastel sunrise sky with soft clouds above a tree-lined path"></div>
    <h2 class="why-title">WHY ASK<br>ABOUT HEAVEN?</h2>
    <div class="qpill qpill--gold"><span class="q">?</span>Many people wonder about life after death. Is there a heaven?</div>
    <div class="qpill qpill--teal"><span class="q">?</span>How can you be sure you'll get there?</div>
    <p class="good-news">The good news is that God has provided clear answers in the Bible. Heaven is not just a destination; it's a promise for those who choose the right path.</p>

    <div class="glass glass--one">For God so loved the world that he gave his one and only Son, that whoever believes in him shall not perish but have eternal life<span class="ref">John 3:16</span></div>
    <span class="qmark" style="left:62px;top:446px;font-size:90px;color:#3f6f8c">“</span>
    <span class="qmark" style="left:420px;top:626px;font-size:90px;color:#3f6f8c">”</span>

    <div class="glass glass--two">Jesus answered, 'I am the way and the truth and the life. No one comes to the Father except through me.<span class="ref">John 14:6</span></div>
    <span class="qmark" style="left:62px;top:676px;font-size:90px;color:#3f6f8c">“</span>
    <span class="qmark" style="left:420px;top:866px;font-size:90px;color:#3f6f8c">”</span>
  </div>

  <div class="panel panel--dark way-panel">
    <h2 class="abs way-title"><span class="script">The Way</span><span class="caps">TO HEAVEN</span></h2>

    <div class="step step--1">Acknowledge Your Need: We all fall short of God's perfect standard. "For all have sinned and fall short of the glory of God<span class="ref">Romans 3:23</span></div>
    <div class="step step--2">Believe in Jesus Christ: Jesus died on the cross to take the punishment for your sins. "But God demonstrates his own love for us in this: While we were still sinners, Christ died for us."<span class="ref">Romans 5:8</span></div>
    <div class="step step--3">Accept God's Gift of Salvation: Eternal life is a free gift, not something you can earn. "For it is by grace you have been saved, through faith and this is not from yourselves, it is the gift of God<span class="ref">Ephesians 2:8–9</span></div>
    <div class="step step--4">Confess and Commit: Pray and invite Jesus into your life as your Savior. "If you declare with your mouth, 'Jesus is Lord,' and believe in your heart that God raised him from the dead, you will be saved<span class="ref">Romans 10:9</span></div>

    <span class="qmark" style="left:100px;top:168px;font-size:50px;color:#a9c8c4">“</span>
    <span class="qmark" style="left:410px;top:326px;font-size:50px;color:#a9c8c4">”</span>
    <span class="qmark" style="left:100px;top:352px;font-size:50px;color:#a9c8c4">“</span>
    <span class="qmark" style="left:410px;top:508px;font-size:50px;color:#a9c8c4">”</span>
    <span class="qmark" style="left:100px;top:532px;font-size:50px;color:#a9c8c4">“</span>
    <span class="qmark" style="left:410px;top:692px;font-size:50px;color:#a9c8c4">”</span>
    <span class="qmark" style="left:100px;top:714px;font-size:50px;color:#a9c8c4">“</span>
    <span class="qmark" style="left:410px;top:876px;font-size:50px;color:#a9c8c4">”</span>

    <p class="abs prayer">Dear God, I know I have sinned and need your forgiveness. I believe Jesus died for my sins and rose from the dead. I trust Him as my Savior and commit my life to Him. Thank you for your grace and the gift of eternal life. Amen</p>
  </div>
</section>

</body>
</html>
```